Private Investment Firm Needs PowerPoint Presentation Template

Design PowerPoint template, take Pinebrook-submitted rough presentation draft, and drop it into new template. See attached Project Brief file for more detail.
Updates

Some decent designs have been submitted but they seem to lack the understanding of our target markets. I am hopeful that more time and feedback will result in better results.

Target Market(s)

Private company owners and intermediaries.

Font styles to use
Serif

Colors
3176b5

Requirements
Must have
• See attached Project Brief.
Nice to have
Should not have
• No B2C fluff--this is a B2B project.

```html
<!DOCTYPE html>
<html lang="en">
<head>
<meta charset="utf-8">
<title>In Summary – Pinebrook Capital</title>
<link rel="stylesheet" href="https://fonts.googleapis.com/css2?family=Montserrat:wght@400;500;600&family=Libre+Caslon+Text:wght@400&display=swap">
<style>
  :root {
    --brand-blue: #1b70bf;
    --text-dark: #1c1c1c;
    --paper: #ffffff;
    --glass-light: #eef3f3;
    --glass-mid: #cfdcdc;
  }
  * { margin: 0; padding: 0; box-sizing: border-box; }
  html, body { width: 1200px; height: 676px; overflow: hidden; background: var(--paper); }
  .slide {
    position: relative;
    width: 1200px;
    height: 676px;
    overflow: hidden;
    background: var(--paper);
    font-family: "Montserrat", Arial, sans-serif;
    color: var(--text-dark);
  }
  .side-band {
    position: absolute; left: 0; top: 0;
    width: 44px; height: 676px;
    background: var(--brand-blue);
  }
  .side-band__url {
    position: absolute;
    left: 22px; top: 336px;
    transform: translate(-50%, -50%) rotate(-90deg);
    font-family: "Libre Caslon Text", Georgia, serif;
    font-size: 15px;
    color: var(--paper);
    white-space: nowrap;
  }
  .edge-band {
    position: absolute; right: 0; top: 0;
    width: 12px; height: 676px;
    background: var(--brand-blue);
  }
  .page-number {
    position: absolute; right: 30px; top: 18px;
    font-family: "Libre Caslon Text", Georgia, serif;
    font-size: 18px;
    color: var(--text-dark);
  }
  .architecture {
    position: absolute;
    left: 470px; top: 300px;
    width: 718px; height: 376px;
    background:
      radial-gradient(ellipse 70% 80% at 100% 100%, var(--glass-mid) 0%, var(--glass-light) 45%, rgba(255,255,255,0) 80%);
  }
  .title {
    position: absolute; left: 86px; top: 80px;
    font-size: 30px; font-weight: 600;
    letter-spacing: 0.2px;
    color: var(--brand-blue);
  }
  .summary-list {
    position: absolute; left: 90px; top: 144px;
    list-style: none;
    font-size: 17px;
    line-height: 28.2px;
    width: 940px;
  }
  .summary-list li { position: relative; padding-left: 24px; }
  .summary-list li::before {
    content: "";
    position: absolute; left: 0; top: 7px;
    width: 13px; height: 13px;
    background: var(--brand-blue);
  }
  .summary-list .sub-list { list-style: none; }
  .summary-list .sub-list li { padding-left: 23px; }
  .summary-list .sub-list li::before { left: 0; }
  .summary-list .sub-list--hang li { padding-left: 0; text-indent: 23px; }
  .summary-list .sub-list--hang li::before { left: 0; }
  .brand {
    position: absolute; left: 68px; top: 618px;
    display: flex; align-items: center; gap: 8px;
  }
  .brand__dot {
    width: 30px; height: 30px; border-radius: 50%;
    background: var(--brand-blue);
  }
  .brand__name {
    font-size: 16px; font-weight: 500;
    letter-spacing: 1.5px;
    color: var(--brand-blue);
  }
</style>
</head>
<body>
<main class="slide">
  <div class="architecture" role="img" aria-label="Photograph of a white modern building facade with tall angled glass fins"></div>

  <aside class="side-band">
    <span class="side-band__url">www.pinebrookcapital.com</span>
  </aside>
  <div class="edge-band"></div>
  <div class="page-number">21</div>

  <h1 class="title">IN SUMMARY</h1>

  <ul class="summary-list">
    <li>There is an alternative to giving up control of your company through an infusion of Non-Control Capital</li>
    <li>All investors are not created equal</li>
    <li>Non-Control Capital investing is a specialty:
      <ul class="sub-list">
        <li>Choose only an investor with decades of Non-Control heritage, experience, and focus<br>(see Questionnaire in the Epilogue section of this presentation)</li>
      </ul>
    </li>
    <li>It means more than just capital:
      <ul class="sub-list sub-list--hang">
        <li>Team up with an accomplished investor who can bring demonstrated growth abilities, not simply write a check</li>
      </ul>
    </li>
    <li>Chemistry between company management and the investor is critical:
      <ul class="sub-list">
        <li>If Pinebrook’s interests are not aligned with management, we don’t invest</li>
      </ul>
    </li>
  </ul>

  <div class="brand">
    <span class="brand__dot"></span>
    <span class="brand__name">PINEBROOK CAPITAL</span>
  </div>
</main>
</body>
</html>
```